House flipping business web site needed

pinecrestholdingsgroup.example.
I am a residential developer in Northern NJ and I am looking for a fresh new updated website. I have an intro video about my company being made now. I don't update it very often but I want an easy format that I can add update photos to on projects I have worked on or homes I renovate for sale.

Target Market(s)

investors into my projects so a portfolio , people looking to sell their homes to me.

Industry/Entity Type

Real Estate Development

Number of Pages Required

4 page

Font styles to use
Serif

Colors
33b8a4
39a9d7
cadf82

Requirements
Must have
• space for an intro video about my company
• a portfolio with pictures and information about each project
• Markets we serve- Morris County, NJ
• My logo- already created
• SEO
• Yes I would like this to function over all platforms. Phone, computer, all platforms.
• history and background page
• I am looking for a completed page that I can upload to the site that hosts my website
Nice to have
• I want something creative, easy to navigate. modern.

```html
<!DOCTYPE html>
<html lang="en">
<head>
<meta charset="utf-8">
<title>Pinecrest Holdings Group – Home Buyers &amp; Renovators, Morris County NJ</title>
<meta name="viewport" content="width=1200">
<link rel="stylesheet" href="https://fonts.googleapis.com/css2?family=Roboto:wght@400;500;700&family=Playfair+Display:ital,wght@0,400;1,700&display=swap">
<style>
:root{
  --teal:#33b8a4;
  --teal-dark:#2aa08e;
  --lime:#cadf82;
  --lime-title:#c3d66f;
  --lime-soft:#dbe9a8;
  --sky:#39a9d7;
  --ink:#333;
  --text:#7a7a7a;
  --panel:#f2f2f2;
  --white:#fff;
}
*{box-sizing:border-box;margin:0;padding:0}
html,body{width:1200px;height:3303px;overflow:hidden}
body{position:relative;background:var(--white);font-family:"Roboto",Arial,sans-serif;color:var(--text)}
.abs{position:absolute}
.btn{position:absolute;display:flex;align-items:center;justify-content:center;background:var(--teal);color:var(--white);font:500 19px "Roboto",sans-serif;letter-spacing:.3px;border-radius:3px}
.section-title{position:absolute;left:0;width:1200px;text-align:center;font:500 40px "Roboto",sans-serif;color:var(--lime-title);letter-spacing:.5px}
.section-title b{color:var(--teal);font-weight:500}

/* header */
.brand{left:77px;top:22px;display:flex;align-items:center;gap:12px}
.brand-mark{width:44px;height:44px;border-radius:50%;background:var(--sky)}
.brand-name{font:700 21px/1.15 "Roboto",sans-serif;color:var(--teal);letter-spacing:.5px}
.call-box{left:709px;top:22px;width:242px;height:88px;background:#eef0f0;border-radius:6px;text-align:center;padding-top:14px}
.call-box .label{font:400 23px "Roboto",sans-serif;color:var(--ink)}
.call-box .phone{font:500 24px "Roboto",sans-serif;color:var(--teal);margin-top:2px}
.agent-photo{left:951px;top:10px;width:160px;height:118px;background:linear-gradient(160deg,#f3e1c9,#e6c9a4 55%,#f8f1e6);border-radius:60px 60px 0 0}

/* nav */
.nav{left:0;top:130px;width:1200px;height:64px;background:var(--lime)}
.nav-item{position:absolute;top:0;height:64px;display:flex;align-items:center;font:400 18px "Roboto",sans-serif;color:var(--ink)}
.nav-item.active{left:77px;width:115px;justify-content:center;background:var(--teal);color:var(--white)}
.search{left:848px;top:7px;width:275px;height:50px;border:2px solid var(--white);display:flex;align-items:center;justify-content:space-between;padding:0 14px;color:var(--white);font-size:15px}

/* hero */
.hero{left:0;top:194px;width:1200px;height:489px;background:linear-gradient(180deg,#8fb6cf 0%,#6e8f5a 30%,#8c8a7c 55%,#5f8a3a 78%,#7cab44 100%)}
.hero-title{left:0;top:130px;width:1200px;text-align:center;font:italic 700 60px/1.12 "Playfair Display",Georgia,serif;color:var(--white);text-shadow:0 3px 8px rgba(0,0,0,.45)}
.hero .btn{left:471px;top:282px;width:251px;height:64px;font-size:20px}
.slide-arrow{position:absolute;top:215px;width:46px;height:46px;border:2px solid rgba(255,255,255,.8);border-radius:50%;display:flex;align-items:center;justify-content:center}

/* welcome */
.welcome-copy{left:160px;top:795px;width:880px;text-align:center;font:400 15.5px/27px "Roboto",sans-serif}

/* about */
.about{left:0;top:1057px;width:1200px;height:440px;background:var(--panel)}
.about-title{left:79px;top:58px;font:500 40px "Roboto",sans-serif;color:var(--lime-title)}
.about-title b{color:var(--teal);font-weight:500}
.about-copy{left:79px;top:108px;width:690px;font:400 15.5px/25px "Roboto",sans-serif;color:#555}
.feature{position:absolute;top:176px;width:220px;text-align:center}
.feature-icon{width:104px;height:104px;margin:0 auto;border-radius:50%;background:var(--lime);display:flex;align-items:center;justify-content:center}
.feature h3{font:500 19px "Roboto",sans-serif;color:var(--ink);margin-top:24px}
.feature p{font:400 14.5px/23px "Roboto",sans-serif;color:#555;margin-top:6px}
.quote-box{left:788px;top:68px;width:335px;height:313px;background:var(--lime);border-radius:4px}
.quote-box h3{position:absolute;left:0;top:26px;width:100%;text-align:center;font:500 31px "Roboto",sans-serif;color:var(--white)}
.quote-box h3 b{color:var(--teal);font-weight:500}
.field{position:absolute;left:27px;width:281px;border:1.5px solid var(--white);color:var(--white);font-size:14px;padding:8px 10px}
.quote-box .btn{left:82px;top:242px;width:178px;height:46px;font-size:18px}

/* video */
.video{left:0;top:1497px;width:1200px;height:366px;background:linear-gradient(180deg,#9fb276 0%,#b9cc7e 40%,#a6bb70 70%,#c5d98a 100%)}
.play{left:558px;top:86px;width:84px;height:84px;border:4px solid var(--white);border-radius:50%;display:flex;align-items:center;justify-content:center}
.video-title{left:0;top:186px;width:1200px;text-align:center;font:400 44px "Playfair Display",Georgia,serif;color:var(--white);letter-spacing:1px}
.video-sub{left:0;top:250px;width:1200px;text-align:center;font:italic 700 22px "Playfair Display",Georgia,serif;color:var(--white)}

/* portfolio */
.portfolio{left:0;top:1863px;width:1200px;height:768px;background:var(--panel)}
.portfolio-copy{left:160px;top:112px;width:880px;text-align:center;font:400 15.5px/27px "Roboto",sans-serif}
.card{position:absolute;width:251px;height:212px}
.card-photo{width:100%;height:154px}
.card-label{height:58px;background:var(--lime);display:flex;align-items:center;justify-content:space-between;padding:0 18px;font:500 19px "Roboto",sans-serif;color:var(--white)}
.card-label.featured{background:var(--teal)}
.portfolio .btn{left:511px;top:647px;width:178px;height:55px;font-size:20px}

/* testimonial */
.testimonial-arrow{position:absolute;top:2758px;width:42px;height:42px;border:2px solid #c9c9c9;border-radius:50%;display:flex;align-items:center;justify-content:center}
.quote-mark{left:560px;top:2747px;width:80px;height:80px;border:3px solid var(--teal);border-radius:50%;display:flex;align-items:center;justify-content:center}
.testimonial-copy{left:170px;top:2846px;width:860px;text-align:center;font:400 16px/28px "Roboto",sans-serif;color:#555}
.client{left:0;top:2906px;width:1200px;text-align:center;font:500 15px "Roboto",sans-serif;color:var(--teal)}

/* footer */
.footer{left:0;top:2983px;width:1200px;height:260px;background:var(--lime);border-top:4px solid var(--teal)}
.f-col{position:absolute;top:36px}
.f-col h4{font:700 15.5px "Roboto",sans-serif;color:var(--teal);letter-spacing:.5px;margin-bottom:16px}
.f-links li{list-style:none;font:400 14.5px/27px "Roboto",sans-serif;color:var(--white)}
.f-row{display:flex;gap:14px;align-items:flex-start;margin-bottom:12px;font:400 14.5px/20px "Roboto",sans-serif;color:var(--white)}
.f-row .ico{width:22px;flex:none;display:flex;justify-content:center}
.f-row strong{color:var(--teal);font-weight:500}
.news{display:flex;gap:14px;margin-bottom:18px}
.news-thumb{width:50px;height:50px;border-radius:50%;background:linear-gradient(135deg,#8d7a63,#c9ab88);flex:none}
.news p{font:400 14px/19px "Roboto",sans-serif;color:var(--white);width:175px}
.news time{display:block;color:var(--teal);font-size:12px}
.newsletter p{font:400 14px/21px "Roboto",sans-serif;color:var(--white);width:250px}
.email-field{margin-top:14px;width:250px;height:42px;background:var(--white);font:400 14px "Roboto",sans-serif;color:#555;padding:12px 10px}
.newsletter .btn{position:static;margin-top:10px;width:166px;height:42px;font-size:18px}
.bottom-bar{left:0;top:3243px;width:1200px;height:60px;background:var(--teal)}
.copyright{left:79px;top:21px;font:400 14px "Roboto",sans-serif;color:var(--white)}
.copyright b{color:var(--lime);font-weight:400}
.social{position:absolute;top:10px;width:40px;height:40px;border-radius:50%;border:2px solid var(--white)}
</style>
</head>
<body>

<!-- Header -->
<header>
  <div class="abs brand">
    <span class="brand-mark"></span>
    <span class="brand-name">PINECREST<br>HOLDINGS GROUP</span>
  </div>
  <div class="abs call-box">
    <div class="label">CONTACT US ON</div>
    <div class="phone">123 456 7890</div>
  </div>
  <div class="abs agent-photo" role="img" aria-label="Photo of a customer service agent wearing a headset"></div>
</header>

<nav class="abs nav">
  <span class="nav-item active">HOME</span>
  <span class="nav-item" style="left:247px">ABOUT US</span>
  <span class="nav-item" style="left:396px">PORTFOLIO</span>
  <span class="nav-item" style="left:557px">CONTACT US</span>
  <div class="abs search">
    <span>Search...</span>
    <svg width="26" height="26" viewBox="0 0 26 26"><circle cx="11" cy="11" r="7.5" fill="none" stroke="#33b8a4" stroke-width="3"/><line x1="16.5" y1="16.5" x2="23" y2="23" stroke="#33b8a4" stroke-width="3.5" stroke-linecap="round"/></svg>
  </div>
</nav>

<!-- Hero -->
<section class="abs hero" role="img" aria-label="Photo of a renovated brick-and-siding family home with a circular driveway and hedges">
  <h1 class="abs hero-title">We will help you get out of<br>your unwanted home</h1>
  <span class="btn">CONTACT US KNOW</span>
  <span class="slide-arrow" style="left:14px"><svg width="14" height="20" viewBox="0 0 14 20"><path d="M10 3 L3 10 L10 17" fill="none" stroke="#fff" stroke-width="2.5"/></svg></span>
  <span class="slide-arrow" style="left:1138px"><svg width="14" height="20" viewBox="0 0 14 20"><path d="M4 3 L11 10 L4 17" fill="none" stroke="#fff" stroke-width="2.5"/></svg></span>
</section>

<!-- Welcome -->
<section>
  <h2 class="section-title" style="top:738px">WELCOME TO <b>PINECREST</b></h2>
  <p class="abs welcome-copy">We only buy and renovate homes in our neighborhoods right here in the Morris County, NJ area. Is a house in your neighborhood an eyesore? Is it vacant, boarded up and a hazard to the neighborhood? Please contact us and we can help transform that property into a beautiful home.<br>Do you need to sell your home fast to avoid foreclosure, have estate home you do not want to fix to put on the market, moving for a job and need your house sold fast. We can help. Contact us now.</p>
  <span class="btn" style="left:511px;top:940px;width:178px;height:57px;font-size:20px">KNOW MORE</span>
</section>

<!-- About -->
<section class="abs about">
  <h2 class="abs about-title">ABOUT <b>US</b></h2>
  <p class="abs about-copy">We are a team of experienced home buyers and renovators in the Morris County, NJ area. Our specialty is purchasing distressed homes and property. We then collaborate with the best talents.</p>

  <div class="feature" style="left:90px">
    <div class="feature-icon"><svg width="44" height="60" viewBox="0 0 44 60"><path d="M8 18 C8 6 36 4 36 18 C36 28 22 28 22 40" fill="none" stroke="#fff" stroke-width="8" stroke-linecap="round"/><circle cx="22" cy="53" r="5" fill="#fff"/></svg></div>
    <h3>How we can help</h3>
    <p>Do you need to sell your home<br>fast to avoid foreclosure.</p>
  </div>
  <div class="feature" style="left:311px">
    <div class="feature-icon"><svg width="46" height="58" viewBox="0 0 46 58"><path d="M4 3 H32 L42 13 V55 H4 Z" fill="none" stroke="#fff" stroke-width="4"/><path d="M11 22 H22 M11 30 H35 M11 38 H35 M11 46 H35" stroke="#fff" stroke-width="3.5"/><circle cx="31" cy="22" r="4" fill="#fff"/></svg></div>
    <h3>Financing</h3>
    <p>We can close quickly and we<br>buy with Cash.</p>
  </div>
  <div class="feature" style="left:546px">
    <div class="feature-icon"><svg width="64" height="40" viewBox="0 0 64 40"><path d="M2 20 C16 0 48 0 62 20 C48 40 16 40 2 20 Z" fill="#fff"/><circle cx="32" cy="20" r="10" fill="#cadf82"/><circle cx="32" cy="20" r="4.5" fill="#fff"/></svg></div>
    <h3>View Latest Homes</h3>
    <p>Pinecrest Holdings Group<br>Coming Soon</p>
  </div>

  <form class="abs quote-box">
    <h3>GET A <b>QUOTE</b></h3>
    <div class="field" style="top:79px;height:36px">Name*</div>
    <div class="field" style="top:123px;height:36px">Email*</div>
    <div class="field" style="top:167px;height:66px">Message*</div>
    <span class="btn">SUBMIT</span>
  </form>
</section>

<!-- Video -->
<section class="abs video" role="img" aria-label="Intro video still: tropical home exterior under a green tint">
  <span class="abs play"><svg width="30" height="36" viewBox="0 0 30 36"><path d="M4 2 L28 18 L4 34 Z" fill="#fff"/></svg></span>
  <h2 class="abs video-title">WATCH THE VIDEO</h2>
  <p class="abs video-sub">We bring excellence to the home buying and renovation business</p>
</section>

<!-- Portfolio -->
<section class="abs portfolio">
  <h2 class="section-title" style="top:55px">OUR <b>PORTFOLIO</b></h2>
  <p class="abs portfolio-copy">Many upgrades to this home, Added a new full bath, family room, office, kitchenette and kids play room in walk out basement with 2 triple french doors. New 1/2 bath was added off of the dining room with large.</p>

  <article class="card" style="left:77px;top:180px"><div class="card-photo" role="img" aria-label="Modern white two-storey house with lawn" style="background:linear-gradient(180deg,#8fb0d8,#d7d9d6 50%,#6d8b4c)"></div><div class="card-label featured">PROJECT TITLE <span>»</span></div></article>
  <article class="card" style="left:343px;top:180px"><div class="card-photo" role="img" aria-label="Family seated on the front steps of their home" style="background:linear-gradient(180deg,#8a4a3a,#b7705a 50%,#7f6a60)"></div><div class="card-label">PROJECT TITLE <span>»</span></div></article>
  <article class="card" style="left:608px;top:180px"><div class="card-photo" role="img" aria-label="Single-storey house with garage under blue sky" style="background:linear-gradient(180deg,#3f6fb8,#9cb9e0 55%,#c9c5bc)"></div><div class="card-label">PROJECT TITLE <span>»</span></div></article>
  <article class="card" style="left:872px;top:180px"><div class="card-photo" role="img" aria-label="Victorian house with green lawn" style="background:linear-gradient(180deg,#9cbbe0,#cdbfa8 50%,#5f8f3b)"></div><div class="card-label">PROJECT TITLE <span>»</span></div></article>

  <article class="card" style="left:77px;top:418px"><div class="card-photo" role="img" aria-label="Contemporary flat-roof house exterior" style="background:linear-gradient(180deg,#e2e0da,#b9a894 55%,#8d8c86)"></div><div class="card-label">PROJECT TITLE <span>»</span></div></article>
  <article class="card" style="left:343px;top:418px"><div class="card-photo" role="img" aria-label="Two-storey suburban house with porch" style="background:linear-gradient(180deg,#a9c3dd,#c9c2b2 55%,#7c9a5a)"></div><div class="card-label">PROJECT TITLE <span>»</span></div></article>
  <article class="card" style="left:608px;top:418px"><div class="card-photo" role="img" aria-label="New white house with gabled roof" style="background:linear-gradient(180deg,#4f86c6,#e8ecef 55%,#7fa06a)"></div><div class="card-label">PROJECT TITLE <span>»</span></div></article>
  <article class="card" style="left:872px;top:418px"><div class="card-photo" role="img" aria-label="Hand holding house keys at a front door" style="background:linear-gradient(135deg,#7b4a2f,#c48a5e 55%,#e8d3bd)"></div><div class="card-label">PROJECT TITLE <span>»</span></div></article>

  <span class="btn">VIEW ALL</span>
</section>

<!-- Testimonial -->
<section>
  <h2 class="section-title" style="top:2682px">WHAT OUR <b>CLIENT SAY</b></h2>
  <span class="testimonial-arrow" style="left:76px"><svg width="12" height="16" viewBox="0 0 12 16"><path d="M9 2 L3 8 L9 14" fill="none" stroke="#aaa" stroke-width="2"/></svg></span>
  <span class="testimonial-arrow" style="left:1080px"><svg width="12" height="16" viewBox="0 0 12 16"><path d="M3 2 L9 8 L3 14" fill="none" stroke="#aaa" stroke-width="2"/></svg></span>
  <span class="abs quote-mark"><svg width="40" height="30" viewBox="0 0 40 30"><path d="M2 30 V16 C2 6 8 1 16 0 V6 C11 7 9 10 9 14 H16 V30 Z M22 30 V16 C22 6 28 1 36 0 V6 C31 7 29 10 29 14 H36 V30 Z" fill="#33b8a4"/></svg></span>
  <p class="abs testimonial-copy">Lorem Ipsum is simply dummy text of the printing and typesetting industry. Lorem Ipsum has been the industry's standard dummy text ever since the Lorem Ipsum is simply dummy.</p>
  <p class="abs client">CLIENT NAME - Dana &amp; Mark</p>
</section>

<!-- Footer -->
<footer class="abs footer">
  <div class="f-col" style="left:79px">
    <h4>USEFUL LINKS</h4>
    <ul class="f-links"><li>» Home</li><li>» About Us</li><li>» Portfolio</li><li>» Contact Us</li></ul>
  </div>
  <div class="f-col" style="left:326px">
    <h4>GET IN TOUCH</h4>
    <div class="f-row"><span class="ico"><svg width="18" height="24" viewBox="0 0 18 24"><path d="M9 23 C3 15 1 12 1 8.5 A8 8 0 0 1 17 8.5 C17 12 15 15 9 23 Z" fill="none" stroke="#33b8a4" stroke-width="2"/><circle cx="9" cy="8.5" r="3" fill="#33b8a4"/></svg></span><span><strong>PINECREST</strong><br>Lorem Ipsum is simple dummy<br>text of print</span></div>
    <div class="f-row"><span class="ico"><svg width="20" height="20" viewBox="0 0 20 20"><path d="M4 1 L8 5 L6 8 C7 11 9 13 12 14 L15 12 L19 16 L16 19 C8 18 2 12 1 4 Z" fill="none" stroke="#33b8a4" stroke-width="2"/></svg></span><span>123 456 7890</span></div>
    <div class="f-row"><span class="ico"><svg width="20" height="20" viewBox="0 0 20 20"><rect x="5" y="1" width="10" height="6" fill="none" stroke="#33b8a4" stroke-width="2"/><rect x="1" y="7" width="18" height="8" fill="none" stroke="#33b8a4" stroke-width="2"/><rect x="5" y="12" width="10" height="7" fill="#cadf82" stroke="#33b8a4" stroke-width="2"/></svg></span><span>123 456 7890</span></div>
    <div class="f-row"><span class="ico"><svg width="20" height="16" viewBox="0 0 20 16"><rect x="1" y="1" width="18" height="14" fill="none" stroke="#33b8a4" stroke-width="2"/><path d="M1 1 L10 9 L19 1" fill="none" stroke="#33b8a4" stroke-width="2"/></svg></span><span>info@pinecrestholdingsgroup.example</span></div>
  </div>
  <div class="f-col" style="left:610px">
    <h4>LATEST NEWS</h4>
    <div class="news"><span class="news-thumb" role="img" aria-label="Author photo"></span><p>Lorem Ipsum is simple text of printing and type.<time>18.10.2016</time></p></div>
    <div class="news"><span class="news-thumb" role="img" aria-label="Author photo"></span><p>Lorem Ipsum is simple text of printing and type.<time>15.10.2016</time></p></div>
  </div>
  <div class="f-col newsletter" style="left:874px">
    <h4>NEWSLETTER</h4>
    <p>Would you like to receive exclusive access to articles, white papers and our regular monthly newsletter?</p>
    <div class="email-field">Enter Email Id</div>
    <span class="btn">SUBSCRIBE</span>
  </div>
</footer>

<div class="abs bottom-bar">
  <p class="abs copyright"><b>©PINECREST HOLDINGS GROUP</b> - 2016. All Rights Reserved</p>
  <span class="social" style="left:917px;background:var(--lime)"></span>
  <span class="social" style="left:962px"></span>
  <span class="social" style="left:1007px"></span>
  <span class="social" style="left:1052px"></span>
  <span class="social" style="left:1097px"></span>
</div>

</body>
</html>
```